Federal IT Consulting Company - Brisolux Consulting Group

We're seeking a skilled web designer to create a modern, bold, and engaging WordPress website for Brisolux Consulting Group, LLC. Our company specializes in federal IT consulting, and our name is a play on "Brightening Solutions." The website should reflect our expertise in the federal technology marketplace and position us as a trusted partner for clients navigating their IT journey.

contact: info@brisoluxgrp-example.com

Current Status

WordPress is already installed on our hosting account
We have an existing logo (may need modernization)

Design Requirements

Style:

Modern and visually striking design
Bold elements to convey confidence and expertise
Incorporate the concept of "brightening solutions" into the design

Features:

Modern UX sliders for dynamic content presentation
Eye-catching, high-quality images (stock photos to be sourced by the designer)
Responsive design for all devices

Color Scheme:

To be proposed by the designer, should align with our brand and convey trust and technological expertise

Logo:

Evaluate our current logo
Create a transparent background version if needed
Propose modernization if deemed necessary

Accessibility:

Ensure design elements are accessible to users with disabilities
Use high contrast ratios for text and background colors
Provide text alternatives for non-text content

Website Structure
Create the following pages, with the possibility of subpages:

Home
Services
About
Contact

Specific Page Requirements
Home Page

Striking hero section with a clear value proposition
Overview of our services
Client testimonials or trust indicators

Services Page

Detailed list of our IT consulting services
Clear explanation of how we help navigate the federal IT landscape

About Page

Company history and mission
Team highlights (if applicable)
Our approach to federal IT consulting

Contact Page

Contact form
Other contact methods (phone, email)

Technical Requirements

Fully responsive design
SEO best practices implemented
Fast loading times
Integration with necessary plugins (to be discussed)
Training on how to update and maintain the site
Full compliance with Web Content Accessibility Guidelines (WCAG) 2.1 Level AA
Adherence to Section 508 standards for federal website accessibility
Implementation of necessary features for ADA compliance
Updates

Designs look the same

Target Market(s)

US Federal Govt customers looking for IT support.

Industry/Entity Type

IT Consulting

Coding

Coded - Design and coding required

Colors
0054AA
0677BA
7BADD7
CADEEF
E8F1F8
0094D4
00A9DD
6FCCEA
C7EBF8
E9F6FB
00AB8E
00BBA5
67D7C9
C6EFE9
E9F9F6

```html
<!DOCTYPE html>
<html lang="en">
<head>
<meta charset="utf-8">
<title>Brisolux Consulting Group</title>
<link href="https://fonts.googleapis.com/css2?family=Lexend:wght@400;500;600;700&family=Poppins:wght@400;500;600&display=swap" rel="stylesheet">
<style>
:root{
  --navy:#2a2878;
  --navy-deep:#1d1a58;
  --purple:#6f67d6;
  --purple-soft:#7b73d8;
  --ink:#141428;
  --body:#3d3d4e;
  --muted:#6b6b7e;
  --tint:#f2f1fb;
  --line:#e4e3f2;
  --star:#f5b700;
  --white:#ffffff;
}
*{box-sizing:border-box;margin:0;padding:0}
html,body{width:1200px;height:3764px;overflow:hidden}
body{position:relative;background:var(--white);font-family:"Poppins",sans-serif;color:var(--ink)}
.abs{position:absolute}
.display{font-family:"Lexend",sans-serif;font-weight:700;text-transform:uppercase;letter-spacing:.5px}
.btn{position:absolute;display:flex;align-items:center;justify-content:center;border-radius:30px;background:var(--navy);color:var(--white);font-family:"Poppins",sans-serif;font-weight:500;font-size:13px}
.rule{position:absolute;height:3px;background:var(--navy);border-radius:2px}
.photo{position:absolute}

/* header */
.site-header{position:absolute;left:0;top:0;width:1200px;height:70px;background:var(--white)}
.brand{display:flex;align-items:center;gap:10px;font-family:"Lexend",sans-serif;font-weight:700;font-size:30px;letter-spacing:1px;text-transform:uppercase}
.brand-dot{width:34px;height:34px;border-radius:50%;background:var(--navy)}
.site-header .brand{position:absolute;left:140px;top:16px;color:var(--navy)}
.nav a{position:absolute;top:26px;font-size:13px;color:var(--ink);text-decoration:none}
.nav a.active{color:var(--purple)}

/* hero */
.hero-photo{left:0;top:70px;width:1200px;height:530px;background:linear-gradient(90deg,#f3f5f8 0%,#eef2f7 35%,#d9e3ef 55%,#c9d6e6 70%,#b8c2c4 85%,#8e9b83 100%)}
.hero h1{position:absolute;left:143px;top:168px;font-size:45px;line-height:49px;color:#0f0f1c}
.hero .sub{position:absolute;left:143px;top:372px;font-family:"Lexend",sans-serif;font-weight:500;font-size:17px;line-height:24px;letter-spacing:3px;text-transform:uppercase;color:#1a1a2a}

/* about */
.about-img1{left:133px;top:683px;width:207px;height:383px;border-radius:90px 0 90px 0;background:linear-gradient(160deg,#e7e9ee,#bfc6d2 60%,#8d94a3)}
.about-img2{left:352px;top:789px;width:248px;height:340px;border-radius:90px 0 90px 0;background:linear-gradient(160deg,#3a3d44,#6a6358 55%,#b7a98e)}
.years-num{left:357px;top:685px;width:70px;height:71px;background:var(--navy);color:var(--white);font-family:"Lexend",sans-serif;font-weight:600;font-size:26px;display:flex;align-items:center;justify-content:center}
.years-label{left:437px;top:685px;width:164px;height:71px;border:1px solid var(--line);border-radius:0 18px 0 18px;padding:12px 18px;font-size:17px;line-height:22px;color:var(--ink)}
.eyebrow{position:absolute;font-family:"Lexend",sans-serif;font-size:20px;text-transform:uppercase;color:var(--navy);letter-spacing:.5px}
.about-copy{left:658px;top:802px;width:405px;font-size:12.5px;line-height:22px;color:var(--body)}
.about-copy p+p{margin-top:6px}

/* services */
.svc-heading{left:143px;top:1244px;font-size:36px;line-height:42px}
.svc-card{position:absolute;top:1381px;width:291px;height:261px;border-radius:12px;overflow:hidden}
.svc-card .photo{inset:0}
.svc-overlay{position:absolute;left:21px;right:21px;bottom:21px;border:1px solid rgba(255,255,255,.8);border-radius:10px;background:rgba(255,255,255,.18);color:var(--white);padding:0 18px}
.svc-overlay h3{font-family:"Lexend",sans-serif;font-weight:400;font-size:15px}
.svc-overlay p{font-size:11px;line-height:17px;margin-top:8px;width:170px}
.arrow-badge{position:absolute;right:18px;width:26px;height:26px;border-radius:50%;background:var(--white);display:flex;align-items:center;justify-content:center}
.round-btn{position:absolute;width:38px;height:38px;border-radius:50%;display:flex;align-items:center;justify-content:center}
.round-btn.outline{border:1.5px solid var(--purple);background:var(--white)}
.round-btn.fill{background:var(--purple)}

/* trust */
.trust{position:absolute;left:0;top:1797px;width:1200px;height:580px;background:var(--tint)}
.center{text-align:center;left:0;width:1200px}
.t-card{position:absolute;top:1997px;width:312px;height:236px;background:var(--white);border-radius:8px;padding:22px 18px}
.t-card .who{display:flex;align-items:center;gap:12px}
.avatar{width:54px;height:54px;border-radius:50%;background:linear-gradient(160deg,#d9d2cb,#9a8e86)}
.who b{display:block;font-family:"Lexend",sans-serif;font-weight:500;font-size:15px;color:var(--ink)}
.who span{font-size:11px;color:var(--muted)}
.quote{position:absolute;right:18px;top:6px;font-family:"Lexend",sans-serif;font-weight:700;font-size:64px;color:var(--purple);line-height:1}
.stars{display:flex;gap:4px;margin-top:12px}
.t-card p{margin-top:12px;font-size:12px;line-height:20px;color:var(--body)}

/* team */
.member{position:absolute;top:2582px;width:183px;text-align:center}
.member .portrait{width:183px;height:183px;border-radius:50%;background:linear-gradient(180deg,#eeeefa,#c9c7ea)}
.member h4{margin-top:22px;font-family:"Lexend",sans-serif;font-weight:500;font-size:15px;color:var(--ink)}
.member .role{font-size:11px;color:var(--purple);margin-top:4px}
.socials{display:flex;justify-content:center;gap:10px;margin-top:14px}
.socials i{width:32px;height:32px;border-radius:50%;background:var(--purple-soft);display:block}

/* cta */
.cta{position:absolute;left:141px;top:3016px;width:917px;height:329px;border-radius:60px;background:var(--purple-soft)}
.cta-person{left:680px;top:2955px;width:295px;height:390px;border-radius:140px 140px 0 0;background:linear-gradient(180deg,#d8b79b,#e2c7a8 40%,#b99a7c)}
.cta h2{position:absolute;left:198px;top:3058px;font-size:35px;line-height:39px;color:var(--white)}
.cta-text{left:198px;top:3196px;width:420px;font-size:12px;line-height:20px;color:var(--white)}

/* footer */
.site-footer{position:absolute;left:0;top:3433px;width:1200px;height:331px;background:var(--navy-deep);color:var(--white)}
.site-footer .brand{position:absolute;left:143px;top:82px;color:var(--white);font-size:40px}
.f-col{position:absolute;top:80px}
.f-col h5{font-family:"Lexend",sans-serif;font-weight:500;font-size:15px;color:#8f88ea;margin-bottom:14px}
.f-col li{list-style:none;font-size:12px;line-height:25px}
.contact-row{display:flex;gap:10px;font-size:12px;line-height:18px;margin-bottom:14px}
.f-rule{position:absolute;left:141px;top:267px;width:917px;height:1px;background:rgba(255,255,255,.2)}
.copyright{position:absolute;left:141px;top:293px;font-size:12px}
.f-social{position:absolute;top:285px;display:flex;gap:12px;left:908px}
.f-social i{width:28px;height:28px;border-radius:50%;background:var(--purple-soft);display:block}
</style>
</head>
<body>

<header class="site-header">
  <div class="brand"><span class="brand-dot"></span>Brisolux</div>
  <nav class="nav">
    <a href="#" class="active" style="left:682px">Home</a>
    <a href="#" style="left:756px">About Us</a>
    <a href="#" style="left:849px">Services</a>
  </nav>
  <a class="btn" style="left:937px;top:15px;width:121px;height:39px">Contact Us</a>
</header>

<section class="hero">
  <div class="photo hero-photo" role="img" aria-label="Photo of the domed federal capitol building under a blue sky with clouds"></div>
  <h1 class="display">Navigate your<br>federal IT<br>journey with<br>confidence</h1>
  <p class="sub">Expert consulting services to<br>guide your IT strategy</p>
  <a class="btn" style="left:141px;top:437px;width:180px;height:43px">Explore Our Services</a>
</section>

<section class="about">
  <div class="photo about-img1" role="img" aria-label="Photo of a consultant presenting charts on a monitor to a colleague"></div>
  <div class="photo about-img2" role="img" aria-label="Photo of a smiling woman working on a laptop in a meeting"></div>
  <div class="abs years-num">15+</div>
  <div class="abs years-label">Year of<br>Experience</div>
  <div class="eyebrow" style="left:658px;top:716px">About</div>
  <div class="abs display" style="left:658px;top:738px;font-size:36px;color:var(--purple)">Brisolux</div>
  <div class="rule" style="left:662px;top:783px;width:70px"></div>
  <div class="abs about-copy">
    <p>Lorem Ipsum is simply dummy text of the printing and typesetting industry. Lorem Ipsum has been the industry's standard dummy text ever since</p>
    <p>Lorem Ipsum is simply dummy text of the printing and typesetting industry. Lorem Ipsum has been the industry's standard dummy text ever since the 1500s, when an unknown printer took a galley of type and scrambled it to make a type specimen book. It has survived not only five centuries, but also the leap into electronic typesetting, remaining essentially unchanged. It was popularised in the 1960s with the release of Letraset sheets containing</p>
  </div>
  <a class="btn" style="left:658px;top:1057px;width:130px;height:42px">Read More</a>
</section>

<section class="services">
  <div class="eyebrow" style="left:141px;top:1212px">Popular Services</div>
  <h2 class="abs display svc-heading"><span style="color:var(--purple)">The best solution</span><br>for your business</h2>
  <div class="rule" style="left:143px;top:1335px;width:70px"></div>
  <a class="btn" style="left:957px;top:1270px;width:101px;height:43px">View All</a>

  <article class="svc-card" style="left:141px">
    <div class="photo" role="img" aria-label="Photo of a dark security operations desk with glowing monitors" style="background:linear-gradient(160deg,#1b1d2c,#3a3f58 50%,#2a1c2a)"></div>
    <div class="svc-overlay" style="top:116px;padding-top:22px">
      <h3>Cybersecurity</h3>
      <p>There are many variations of passages of Lorem Ipsum available.</p>
      <span class="arrow-badge" style="top:78px"><svg width="12" height="12" viewBox="0 0 12 12"><path d="M3 9L9 3M4 3h5v5" stroke="#2a2878" stroke-width="1.5" fill="none"/></svg></span>
    </div>
  </article>
  <article class="svc-card" style="left:454px">
    <div class="photo" role="img" aria-label="Photo of a hand touching a glowing cloud computing interface" style="background:linear-gradient(160deg,#0f2b45,#2f6d96 50%,#173a5c)"></div>
    <div class="svc-overlay" style="height:62px;display:flex;align-items:center">
      <h3>Cloud Services</h3>
      <span class="arrow-badge" style="top:17px"><svg width="12" height="12" viewBox="0 0 12 12"><path d="M3 9L9 3M4 3h5v5" stroke="#2a2878" stroke-width="1.5" fill="none"/></svg></span>
    </div>
  </article>
  <article class="svc-card" style="left:767px">
    <div class="photo" role="img" aria-label="Photo of a team meeting around a conference table with laptops" style="background:linear-gradient(160deg,#6a7a4c,#a59775 50%,#4b3d30)"></div>
    <div class="svc-overlay" style="height:62px;display:flex;align-items:center">
      <h3>IT Strategy Consulting</h3>
      <span class="arrow-badge" style="top:17px"><svg width="12" height="12" viewBox="0 0 12 12"><path d="M3 9L9 3M4 3h5v5" stroke="#2a2878" stroke-width="1.5" fill="none"/></svg></span>
    </div>
  </article>

  <span class="round-btn outline" style="left:549px;top:1675px"><svg width="18" height="12" viewBox="0 0 18 12"><path d="M17 6H2M6 1L1 6l5 5" stroke="#6f67d6" stroke-width="1.6" fill="none"/></svg></span>
  <span class="round-btn fill" style="left:613px;top:1675px"><svg width="18" height="12" viewBox="0 0 18 12"><path d="M1 6h15M12 1l5 5-5 5" stroke="#fff" stroke-width="1.6" fill="none"/></svg></span>
</section>

<section class="trust"></section>
<h2 class="abs display center" style="top:1856px;font-size:36px"><span style="color:var(--purple)">Trusted client</span> and partners</h2>
<div class="rule" style="left:565px;top:1906px;width:70px"></div>
<p class="abs center" style="top:1925px;font-size:12.5px;line-height:22px;color:var(--body)">Duis aute irure dolor in reprehenderit in voluptate velit esse cillum dolore eu fugiat nulla pariatur. Excepteur sint occaecat cupidatat non proident,<br>sunt in culpa qui officia deserunt mollit anim id est laborum.</p>

<div class="t-card" style="left:-222px">
  <span class="quote">”</span>
  <p style="margin-top:90px">Lorem ipsum dolor sit amet, consectetur sit adipiscing elit, sed do eiusmod tempor ut incididunt ut labore et dolore magna amet aliqua. Ut enim ad minim veniam, quis dolor</p>
</div>
<div class="t-card" style="left:111px">
  <div class="who"><span class="avatar" role="img" aria-label="Client portrait"></span><div><b>Colin Farrow</b><span>Lorem Ipsum</span></div></div>
  <span class="quote">”</span>
  <div class="stars"><svg width="76" height="12" viewBox="0 0 76 12"><g fill="#f5b700"><path id="s" d="M6 0l1.8 3.9 4.2.4-3.2 2.8 1 4.1L6 9.1 2.2 11.2l1-4.1L0 4.3l4.2-.4z"/><use href="#s" x="16"/><use href="#s" x="32"/><use href="#s" x="48"/><use href="#s" x="64"/></g></svg></div>
  <p>Lorem ipsum dolor sit amet, consectetur sit adipiscing elit, sed do eiusmod tempor ut incididunt ut labore et dolore magna amet aliqua. Ut enim ad minim veniam, quis dolor nostrud exercitation ullamco.</p>
</div>
<div class="t-card" style="left:444px">
  <div class="who"><span class="avatar" role="img" aria-label="Client portrait"></span><div><b>Ines Calloway</b><span>Lorem Ipsum</span></div></div>
  <span class="quote">”</span>
  <div class="stars"><svg width="76" height="12" viewBox="0 0 76 12"><g fill="#f5b700"><use href="#s"/><use href="#s" x="16"/><use href="#s" x="32"/><use href="#s" x="48"/><use href="#s" x="64"/></g></svg></div>
  <p>Lorem ipsum dolor sit amet, consectetur sit adipiscing elit, sed do eiusmod tempor ut incididunt ut labore et dolore magna amet aliqua. Ut enim ad minim veniam, quis dolor nostrud exercitation ullamco.</p>
</div>
<div class="t-card" style="left:777px">
  <div class="who"><span class="avatar" role="img" aria-label="Client portrait"></span><div><b>Maren Holt</b><span>Lorem Ipsum</span></div></div>
  <span class="quote">”</span>
  <div class="stars"><svg width="76" height="12" viewBox="0 0 76 12"><g fill="#f5b700"><use href="#s"/><use href="#s" x="16"/><use href="#s" x="32"/><use href="#s" x="48"/><use href="#s" x="64"/></g></svg></div>
  <p>Lorem ipsum dolor sit amet, consectetur sit adipiscing elit, sed do eiusmod tempor ut incididunt ut labore et dolore magna amet aliqua. Ut enim ad minim veniam, quis dolor nostrud exercitation ullamco.</p>
</div>
<div class="t-card" style="left:1110px">
  <div class="who"><span class="avatar" role="img" aria-label="Client portrait"></span></div>
  <div class="stars"><svg width="76" height="12" viewBox="0 0 76 12"><g fill="#f5b700"><use href="#s"/><use href="#s" x="16"/><use href="#s" x="32"/><use href="#s" x="48"/><use href="#s" x="64"/></g></svg></div>
  <p>Lorem ipsum dolor sit amet, consectetur sit adipiscing elit, sed do eiusmod tempor ut incididunt ut labore et dolore magna amet aliqua. Ut enim ad minim veniam, quis dolor nostrud exercitation ullamco.</p>
</div>
<span class="round-btn outline" style="left:558px;top:2262px;width:36px;height:36px;border-color:var(--line)"><svg width="14" height="10" viewBox="0 0 14 10"><path d="M13 5H2M5 1L1 5l4 4" stroke="#141428" stroke-width="1.6" fill="none"/></svg></span>
<span class="round-btn fill" style="left:607px;top:2262px;width:36px;height:36px"><svg width="14" height="10" viewBox="0 0 14 10"><path d="M1 5h11M9 1l4 4-4 4" stroke="#fff" stroke-width="1.6" fill="none"/></svg></span>

<section class="team">
  <div class="eyebrow center" style="top:2459px">Our Team</div>
  <h2 class="abs display center" style="top:2492px;font-size:36px"><span style="color:var(--purple)">Meet the</span> our experts</h2>
  <div class="rule" style="left:565px;top:2547px;width:70px"></div>
  <div class="member" style="left:175px"><div class="portrait" role="img" aria-label="Portrait of a team member in a dark blazer"></div><h4>Tessa Brandt</h4><div class="role">Web Designer</div><div class="socials"><i></i><i></i></div></div>
  <div class="member" style="left:397px"><div class="portrait" role="img" aria-label="Portrait of a team member in a suit and red tie"></div><h4>Julian Okafor</h4><div class="role">Web Designer</div><div class="socials"><i></i><i></i></div></div>
  <div class="member" style="left:619px"><div class="portrait" role="img" aria-label="Portrait of a team member in a light blue shirt"></div><h4>Priya Navar</h4><div class="role">Web Designer</div><div class="socials"><i></i><i></i></div></div>
  <div class="member" style="left:842px"><div class="portrait" role="img" aria-label="Portrait of a team member in a navy suit"></div><h4>Owen Marsh</h4><div class="role">Web Designer</div><div class="socials"><i></i><i></i></div></div>
</section>

<section>
  <div class="cta"></div>
  <div class="photo cta-person" role="img" aria-label="Photo of a smiling consultant in a beige suit holding a laptop"></div>
  <h2 class="display">We are consulting<br>group we make<br>future!</h2>
  <div class="rule" style="left:198px;top:3180px;width:70px;background:var(--white)"></div>
  <p class="abs cta-text">There are many variations of passages of Lorem Ipsum available, but the majority have suffered alteration in some form.</p>
  <a class="btn" style="left:198px;top:3250px;width:145px;height:42px;background:var(--white);color:var(--purple)">Get Started Now</a>
  <svg class="abs" style="left:360px;top:3240px" width="130" height="100" viewBox="0 0 130 100"><path d="M115 15L95 25l8 4zM103 29l-2 10 6-7" stroke="#fff" stroke-width="1.4" fill="none"/><path d="M95 28C70 40 40 30 25 55 15 72 20 85 10 95" stroke="#fff" stroke-width="1.2" stroke-dasharray="4 4" fill="none"/></svg>
</section>

<footer class="site-footer">
  <div class="brand"><span class="brand-dot" style="background:var(--purple-soft);width:40px;height:40px"></span>Brisolux</div>
  <div class="f-col" style="left:510px"><h5>Quick Links</h5><ul><li>Home</li><li>About Us</li><li>Services</li></ul></div>
  <div class="f-col" style="left:673px;top:77px"><h5>Resources</h5><ul><li>Privacy Policy</li><li>Terms Of Service</li></ul></div>
  <div class="f-col" style="left:852px;top:77px;width:210px">
    <h5>Contact Info</h5>
    <div class="contact-row"><svg width="14" height="18" viewBox="0 0 14 18"><path d="M7 1a6 6 0 0 0-6 6c0 4.5 6 10 6 10s6-5.5 6-10a6 6 0 0 0-6-6zm0 8.2A2.2 2.2 0 1 1 7 4.8a2.2 2.2 0 0 1 0 4.4z" fill="#8f88ea"/></svg><span>123 Lorem Ipsum Dummy,<br>#567 Dummy Road 1234</span></div>
    <div class="contact-row"><svg width="16" height="12" viewBox="0 0 16 12"><rect x="0" y="0" width="16" height="12" rx="1.5" fill="#8f88ea"/><path d="M1 1l7 5 7-5" stroke="#1d1a58" stroke-width="1.3" fill="none"/></svg><span>info@brisoluxgrp-example.com</span></div>
    <div class="contact-row"><svg width="15" height="15" viewBox="0 0 15 15"><path d="M3.2 1l2.3 3-1.3 1.8a9 9 0 0 0 5 5l1.8-1.3 3 2.3-1.5 2.2C7 14 1 8 1 2.5z" fill="#8f88ea"/></svg><span>123-456-7890</span></div>
  </div>
  <div class="f-rule"></div>
  <p class="copyright">© 2024 Brisolux Consulting Group. All rights reserved.</p>
  <div class="f-social"><i></i><i></i><i></i><i></i></div>
</footer>

</body>
</html>
```